Web Design Project for a new download application :-)

We need a website design and a logo design for a new website and desktop application.
The Website will be www.Gruvlo.com
The installed application will be: Gruvlo

Gruvlo is a desktop application that searches and finds all kind of Media files (Movies, Games, Songs, software, etc..)
Gruvlo will also manage the download process for the selected files.
Gruvlo automates the whole search and download process.

User Flow:
users will initially visit the website.
user will download the application from the website
user will install the application on his computer.
user will run and use the application.

What makes our software special:
-Great search engine for searching media files.
-Very high speed downloads. maximum speeds.
-Allow used to Search by: file type, size, date, format
-Pause and resume downloads
-Get any file you want instantly.
-Unlimited Downloads.

We will need:
Logo
WebSite Design
Icons for the desktop application.

we need only PSDs - no codded pages are needed !

Design to the following screen Size & resolution: 1024 x 768

Target Market(s)

movies and music lovers.
users who download movies, games, softwares, music etc...

Industry/Entity Type

Software

Requirements
Must have
• must have download button

```html
<!DOCTYPE html>
<html lang="en">
<head>
<meta charset="utf-8">
<title>Gruvlo – Search and download media files</title>
<link href="https://fonts.googleapis.com/css2?family=Source+Sans+3:ital,wght@0,400;0,600;1,400&family=Arimo:wght@400;700&display=swap" rel="stylesheet">
<style>
  :root {
    --header-top: #4a7fc4;
    --header-bottom: #2d5ea3;
    --nav-active: #1e9ee0;
    --nav-text: #ffffff;
    --hero-top: #ffffff;
    --hero-bottom: #e9ecef;
    --heading-grey: #6b6b6b;
    --brand-blue: #2f63b0;
    --feature-blue: #1a4fa8;
    --body-grey: #6e6e6e;
    --divider: #e6e6e6;
    --footer-bg: #000000;
    --footer-text: #8a8a8a;
    --footer-link: #2e9fe6;
    --check-green: #7fbf4a;
    --dot-grey: #a8a8a0;
    --dot-green: #6cb31e;
    --button-top: #8fd14f;
    --button-bottom: #3f9a1c;
    --button-edge: #357f18;
  }
  * { margin: 0; padding: 0; box-sizing: border-box; }
  html, body { width: 1200px; height: 826px; overflow: hidden; }
  body { position: relative; background: #fff; font-family: "Arimo", Arial, sans-serif; }

  .site-header {
    position: absolute; left: 0; top: 0; width: 1200px; height: 58px;
    background: linear-gradient(var(--header-top), var(--header-bottom));
    box-shadow: 0 2px 4px rgba(0,0,0,.25); z-index: 2;
  }
  .brand { position: absolute; left: 148px; top: 9px; display: flex; align-items: center; gap: 10px; }
  .brand-mark { width: 30px; height: 30px; background: #fff; border-radius: 3px; }
  .brand-name { color: #fff; font-size: 32px; font-weight: 400; line-height: 40px; }
  .main-nav { position: absolute; left: 328px; top: 0; display: flex; height: 58px; }
  .main-nav a {
    color: var(--nav-text); text-decoration: none; font-weight: 700; font-size: 13px;
    line-height: 58px; padding: 0 17px;
  }
  .main-nav a.is-active { background: var(--nav-active); padding: 0 18px; }
  .language-select {
    position: absolute; left: 888px; top: 14px; width: 165px; height: 28px;
    background: #2b5591; border: 1px solid #24497f; color: #c9d6e8; font-size: 12px;
    display: flex; align-items: center;
  }
  .language-flag { width: 15px; height: 10px; background: #c8d2e6; margin: 0 9px 0 7px; }
  .language-toggle {
    position: absolute; right: 0; top: 0; width: 19px; height: 26px; background: #5ea4e0;
  }
  .language-toggle svg { position: absolute; left: 5px; top: 11px; }

  .hero {
    position: absolute; left: 0; top: 58px; width: 1200px; height: 416px;
    background: linear-gradient(var(--hero-top) 0%, #f6f7f8 80%, var(--hero-bottom) 100%);
    border-bottom: 1px solid #d9dcdf;
  }
  .hero-title {
    position: absolute; left: 166px; top: 176px; font-family: "Source Sans 3", sans-serif;
    font-size: 26px; font-weight: 400; color: var(--heading-grey); line-height: 32px;
    text-shadow: 0 1px 2px rgba(0,0,0,.15); white-space: nowrap;
  }
  .hero-title span { color: var(--brand-blue); }
  .steps { position: absolute; left: 139px; top: 224px; list-style: none; }
  .steps li {
    font-family: "Source Sans 3", sans-serif; font-size: 19px; color: var(--heading-grey);
    height: 34px; display: flex; align-items: center; gap: 10px;
    text-shadow: 0 1px 2px rgba(0,0,0,.12);
  }
  .steps em { font-style: italic; }
  .download-button {
    position: absolute; left: 168px; top: 336px; height: 38px; padding: 0 14px 0 18px;
    display: flex; align-items: center; gap: 12px;
    background: linear-gradient(var(--button-top), var(--button-bottom));
    border: 1px solid var(--button-edge); border-radius: 5px;
    color: #fff; font-family: "Arimo", Arial, sans-serif; font-weight: 700; font-size: 15px;
    letter-spacing: .5px; text-decoration: none;
    box-shadow: 0 2px 4px rgba(0,0,0,.2), inset 0 1px 0 rgba(255,255,255,.35);
  }
  .hero-visual {
    position: absolute; left: 570px; top: 8px; width: 536px; height: 365px;
    background: radial-gradient(ellipse at 55% 45%, #f5f5f5 0%, #f2c94c 30%, #e86a8e 55%, #8b4fb0 72%, rgba(255,255,255,0) 90%);
    opacity: .55;
  }
  .slider-dots { position: absolute; left: 553px; top: 382px; display: flex; gap: 5px; }
  .slider-dots span {
    width: 15px; height: 15px; border-radius: 50%; background: var(--dot-grey);
    box-shadow: inset 0 -2px 3px rgba(0,0,0,.2);
  }
  .slider-dots span.is-current { background: var(--dot-green); }

  .features { position: absolute; left: 0; top: 475px; width: 1200px; height: 258px; background: #fff; }
  .feature { position: absolute; top: 45px; width: 290px; }
  .feature-icon { position: absolute; left: 0; top: 0; width: 78px; height: 75px; border-radius: 8px; }
  .feature-title {
    position: absolute; top: 22px; font-size: 16px; line-height: 19px; color: var(--feature-blue);
    font-weight: 400; white-space: nowrap;
  }
  .feature-text {
    position: absolute; left: 0; top: 99px; width: 260px; font-size: 13px; line-height: 22.5px; color: var(--body-grey);
  }
  .divider {
    position: absolute; top: 36px; width: 6px; height: 192px;
    background: linear-gradient(90deg, var(--divider), rgba(255,255,255,0));
  }
  .carousel-arrow { position: absolute; top: 113px; }

  .site-footer {
    position: absolute; left: 0; top: 733px; width: 1200px; height: 93px; background: var(--footer-bg);
    font-size: 13px; color: var(--footer-text);
  }
  .footer-links { position: absolute; left: 188px; top: 27px; }
  .footer-links a { color: var(--footer-text); text-decoration: none; }
  .footer-links .sep { margin: 0 6px; }
  .copyright { position: absolute; left: 188px; top: 50px; }
  .copyright a { color: var(--footer-link); text-decoration: none; }
</style>
</head>
<body>
  <header class="site-header">
    <div class="brand"><span class="brand-mark"></span><span class="brand-name">Gruvlo</span></div>
    <nav class="main-nav">
      <a class="is-active" href="#">HOME</a>
      <a href="#">DOWNLOAD</a>
      <a href="#">SUPPORT</a>
      <a href="#">AFFILIATES</a>
    </nav>
    <div class="language-select">
      <span class="language-flag"></span>English
      <span class="language-toggle"><svg width="9" height="5" viewBox="0 0 9 5"><path d="M0 0h9L4.5 5z" fill="#1d3f73"/></svg></span>
    </div>
  </header>

  <section class="hero">
    <h1 class="hero-title">Simple steps to search with <span>Gruvlo</span></h1>
    <ul class="steps">
      <li><svg width="20" height="20" viewBox="0 0 20 20"><path d="M2 11l5 6L18 3" fill="none" stroke="var(--check-green)" stroke-width="2.5"/></svg><span><em>download</em> Gruvlo apps from website</span></li>
      <li><svg width="20" height="20" viewBox="0 0 20 20"><path d="M2 11l5 6L18 3" fill="none" stroke="var(--check-green)" stroke-width="2.5"/></svg><span><em>install</em> it to your desktop</span></li>
      <li><svg width="20" height="20" viewBox="0 0 20 20"><path d="M2 11l5 6L18 3" fill="none" stroke="var(--check-green)" stroke-width="2.5"/></svg><span><em>run</em> and <em>search</em> the media files</span></li>
    </ul>
    <a class="download-button" href="#">DOWNLOAD
      <svg width="16" height="18" viewBox="0 0 16 18"><path d="M5 0h6v8h4l-7 8-7-8h4z" fill="#fff"/></svg>
    </a>
    <div class="hero-visual" role="img" aria-label="Illustration of a desktop computer showing the Gruvlo website in front of a rainbow, clouds and colourful swirls"></div>
    <div class="slider-dots"><span class="is-current"></span><span></span><span></span><span></span><span></span></div>
  </section>

  <section class="features">
    <svg class="carousel-arrow" style="left:79px" width="24" height="26" viewBox="0 0 24 26"><path d="M20 1L4 13l16 12" fill="none" stroke="#b8b8b8" stroke-width="4"/></svg>

    <article class="feature" style="left:158px">
      <div class="feature-icon" role="img" aria-label="Film reel with magnifying glass icon" style="background:linear-gradient(135deg,#c9d4de,#5c7b98)"></div>
      <h2 class="feature-title" style="left:87px">Great search engine for<br>searching media files</h2>
      <p class="feature-text">Lorem ipsum dolor sit amet, consectetur adipiscing elit. Etiam auctor tortor tellus, ut consectetur arcu.</p>
    </article>
    <div class="divider" style="left:439px"></div>

    <article class="feature" style="left:479px">
      <div class="feature-icon" role="img" aria-label="Green download arrow over a globe and hard drive icon" style="width:56px;background:linear-gradient(#8fcf5a,#4a86c8 60%,#cfd4d8)"></div>
      <h2 class="feature-title" style="left:62px">Very high speed downloads<br>maximum speeds.</h2>
      <p class="feature-text">Lorem ipsum dolor sit amet, consectetur adipiscing elit. Etiam auctor tortor tellus, ut consectetur arcu.</p>
    </article>
    <div class="divider" style="left:761px"></div>

    <article class="feature" style="left:800px">
      <div class="feature-icon" role="img" aria-label="Files, disc, music note and magnifying glass icon" style="width:107px;background:linear-gradient(135deg,#e8ecef,#9fc46a 55%,#8a9aa8)"></div>
      <h2 class="feature-title" style="left:118px">Search by file type,<br>size, date, format</h2>
      <p class="feature-text">Lorem ipsum dolor sit amet, consectetur adipiscing elit. Etiam auctor tortor tellus, ut consectetur arcu.</p>
    </article>

    <svg class="carousel-arrow" style="left:1097px" width="24" height="26" viewBox="0 0 24 26"><path d="M4 1l16 12L4 25" fill="none" stroke="#b8b8b8" stroke-width="4"/></svg>
  </section>

  <footer class="site-footer">
    <nav class="footer-links">
      <a href="#">Home</a><span class="sep">|</span><a href="#">Download</a><span class="sep">|</span><a href="#">Support</a><span class="sep">|</span>&nbsp;<a href="#">Affiliates</a><span class="sep">|</span><a href="#">Contact Us</a><span class="sep">|</span><a href="#">Privacy Policy</a><span class="sep">|</span><a href="#">License Agreement</a>
    </nav>
    <p class="copyright">Copyright © <a href="#">Gruvlo.com</a> 2011.&nbsp; All rights reserved.</p>
  </footer>
</body>
</html>
```